Stationery Design Project

I need a design that is simple, clean and modern, in square style, bold font.
The majority of the design needs to be White and Black with a splash of Red colour.
I would like a design for business cards and letter heads with the following information.
Name, Title, Phone, Fax, Email, Website and company ABN number

Target Market(s)

25 to 65 years old real estate clients

Industry/Entity Type

Business

Requirements
Must have
• All designs must incorporate Company Logo, Name, Title, Phone, Fax, Email, Website and company ABN number

```html
<!DOCTYPE html>
<html lang="en">
<head>
<meta charset="utf-8">
<title>Northgate Realty – Business Card</title>
<link rel="stylesheet" href="https://fonts.googleapis.com/css2?family=Source+Sans+3:wght@400;700&display=swap">
<style>
  :root {
    --backdrop: #d8d3cd;
    --card: #ffffff;
    --ink: #1e1e1e;
    --muted: #555555;
    --accent: #d7262e;
  }
  * { box-sizing: border-box; margin: 0; padding: 0; }
  html, body {
    width: 1200px;
    height: 402px;
    overflow: hidden;
    background: var(--backdrop);
    font-family: "Source Sans 3", "Segoe UI", Arial, sans-serif;
    color: var(--ink);
  }
  .stage { position: relative; width: 1200px; height: 402px; }
  .card {
    position: absolute;
    top: 56px;
    width: 511px;
    height: 291px;
    background: var(--card);
    border-radius: 24px;
    box-shadow: 0 2px 6px rgba(0,0,0,.18);
  }
  .card--front { left: 66px; }
  .card--back { left: 625px; display: flex; align-items: center; justify-content: center; }

  .brand { display: flex; align-items: center; gap: 10px; color: var(--ink); font-weight: 700; letter-spacing: .04em; }
  .brand__mark { background: var(--accent); flex: none; }
  .brand--small { position: absolute; left: 36px; top: 66px; font-size: 30px; }
  .brand--small .brand__mark { width: 16px; height: 16px; }
  .brand--large { font-size: 46px; gap: 14px; }
  .brand--large .brand__mark { width: 24px; height: 24px; }

  .person { position: absolute; right: 30px; top: 94px; text-align: right; }
  .person__name { color: var(--accent); font-weight: 700; font-size: 16px; line-height: 18px; }
  .person__title { color: var(--muted); font-size: 12.5px; line-height: 14px; }

  .contacts { position: absolute; right: 30px; top: 197px; list-style: none; }
  .contacts li { display: flex; justify-content: flex-end; align-items: center; gap: 4px; font-size: 13px; line-height: 16.5px; color: var(--ink); }
  .contacts svg { width: 11px; height: 11px; flex: none; }

  .address { position: absolute; left: 34px; top: 234px; font-size: 12.5px; line-height: 15px; color: var(--ink); }
</style>
</head>
<body>
<main class="stage">
  <section class="card card--front" aria-label="Card front">
    <div class="brand brand--small"><span class="brand__mark"></span>NORTHGATE</div>

    <div class="person">
      <p class="person__name">Your name</p>
      <p class="person__title">Title</p>
    </div>

    <ul class="contacts">
      <li>123-456-7890
        <svg viewBox="0 0 12 12" aria-hidden="true"><circle cx="6" cy="6" r="6" fill="var(--accent)"/><path d="M4 3.2l1.2 1.3-.6.8c.4.9 1 1.5 1.9 1.9l.8-.6 1.3 1.2-.8 1C5.5 8.6 3.4 6.5 3.2 4z" fill="#fff"/></svg>
      </li>
      <li>123-456-7890
        <svg viewBox="0 0 12 12" aria-hidden="true"><circle cx="6" cy="6" r="6" fill="var(--accent)"/><rect x="4.2" y="2.6" width="3.6" height="6.8" rx=".6" fill="#fff"/><rect x="4.9" y="3.4" width="2.2" height="4.4" fill="var(--accent)"/></svg>
      </li>
      <li>info@mailbox.com
        <svg viewBox="0 0 12 12" aria-hidden="true"><circle cx="6" cy="6" r="6" fill="var(--accent)"/><rect x="3" y="4" width="6" height="4.2" fill="#fff"/><path d="M3 4l3 2.3L9 4" fill="none" stroke="var(--accent)" stroke-width=".7"/></svg>
      </li>
      <li>www.website.com
        <svg viewBox="0 0 12 12" aria-hidden="true"><circle cx="6" cy="6" r="6" fill="var(--accent)"/><circle cx="6" cy="6" r="3" fill="none" stroke="#fff" stroke-width=".8"/><path d="M3 6h6M6 3c-1.3 1.6-1.3 4.4 0 6M6 3c1.3 1.6 1.3 4.4 0 6" fill="none" stroke="#fff" stroke-width=".6"/></svg>
      </li>
    </ul>

    <address class="address" style="font-style:normal">
      Street Name, City Name<br>
      State, City Zip Code
    </address>
  </section>

  <section class="card card--back" aria-label="Card back">
    <div class="brand brand--large"><span class="brand__mark"></span>NORTHGATE</div>
  </section>
</main>
</body>
</html>
```